Executive Business Card for Healthcare Company [Need Today]

I need a business card design for a healthcare company. The only branding the company has thus far is a logo. The cards will be utilized by company executives. The design I envision will be vibrant and appealing but with a corporate feel. They shouldn't be too casual or playful. I would like to complete this project TODAY if possible.

Target Market(s)

Healthcare vendors, other executives in healthcare and pharmaceuticals

Industry/Entity Type

Pharmaceutical

Contact Information for Business Card

See attachment

Font styles to use
Serif
Sans Serif

Colors

Designer to choose colors to be used in the design.

```html
<!DOCTYPE html>
<html lang="en">
<head>
<meta charset="utf-8">
<title>Quennick Therapeutics – Business Card</title>
<link href="https://fonts.googleapis.com/css2?family=Arimo:wght@400;700&display=swap" rel="stylesheet">
<style>
  :root {
    --teal: #3bbfc8;
    --mint: #6cc49a;
    --ink: #1e1e1e;
    --paper: #ffffff;
    --backdrop: #eceae6;
    --sans: "Arimo", Arial, sans-serif;
  }
  html, body {
    margin: 0;
    width: 1200px;
    height: 900px;
    overflow: hidden;
    background: var(--backdrop);
    font-family: var(--sans);
  }
  .stage { position: relative; width: 1200px; height: 900px; }
  .card {
    position: absolute;
    width: 560px;
    height: 320px;
    box-shadow: 0 6px 18px rgba(0,0,0,.18);
    overflow: hidden;
  }
  .brand {
    position: absolute;
    display: flex;
    align-items: center;
    gap: 12px;
    white-space: nowrap;
  }
  .brand-mark {
    flex: none;
    border-radius: 50%;
    border: 3px solid currentColor;
    box-sizing: border-box;
  }
  .brand-rule { flex: none; width: 1px; background: currentColor; opacity: .8; }
  .brand-name { font-weight: 400; letter-spacing: .3px; }

  /* Front */
  .card-front { left: 90px; top: 100px; background: var(--teal); }
  .card-front .brand {
    color: var(--paper);
    left: 50%; top: 50%;
    transform: translate(-50%, -50%);
  }
  .card-front .brand-mark { width: 90px; height: 90px; }
  .card-front .brand-rule { height: 70px; }
  .card-front .brand-name { font-size: 30px; }

  /* Back */
  .card-back { left: 550px; top: 480px; background: var(--paper); }
  .card-back .brand { color: var(--teal); right: 24px; top: 34px; gap: 10px; }
  .card-back .brand-mark { width: 54px; height: 54px; border-color: var(--mint); }
  .card-back .brand-rule { height: 48px; }
  .card-back .brand-name { font-size: 20px; }
  .wave { position: absolute; inset: 0; }
  .person { position: absolute; left: 34px; top: 44px; }
  .person-name { margin: 0; font-size: 20px; font-weight: 700; color: var(--teal); letter-spacing: .3px; }
  .person-title { margin: 2px 0 0 4px; font-size: 13px; color: var(--ink); }
  .contacts {
    position: absolute; left: 38px; top: 128px;
    list-style: none; margin: 0; padding: 0;
  }
  .contacts li {
    display: flex; align-items: center; gap: 5px;
    font-size: 15px; color: var(--ink); line-height: 21px;
  }
  .contacts svg { width: 16px; height: 16px; flex: none; }
  .company { position: absolute; left: 44px; top: 200px; }
  .company-name { margin: 0; font-size: 16px; font-weight: 700; color: var(--mint); }
  .company-address { margin: 2px 0 0; font-size: 15px; color: var(--ink); }
</style>
</head>
<body>
<main class="stage">
  <section class="card card-front" aria-label="Card front">
    <div class="brand">
      <span class="brand-mark"></span>
      <span class="brand-rule"></span>
      <span class="brand-name">Quennick Therapeutics</span>
    </div>
  </section>

  <section class="card card-back" aria-label="Card back">
    <svg class="wave" viewBox="0 0 560 320" preserveAspectRatio="none" aria-hidden="true">
      <path d="M560 150 C470 160 400 205 300 255 C220 292 150 300 70 300 L40 320 L560 320 Z" fill="var(--mint)"/>
      <path d="M0 282 C110 300 220 290 330 240 C380 218 410 200 450 186 C400 212 360 235 320 258 C220 310 110 312 0 300 Z" fill="var(--teal)"/>
    </svg>

    <div class="person">
      <h1 class="person-name">DANIEL MOREAU</h1>
      <p class="person-title">Senior Director of Marketing</p>
    </div>

    <div class="brand">
      <span class="brand-mark"></span>
      <span class="brand-rule"></span>
      <span class="brand-name">Quennick Therapeutics</span>
    </div>

    <ul class="contacts">
      <li>
        <svg viewBox="0 0 16 16" aria-label="Phone"><circle cx="8" cy="8" r="7.5" fill="var(--mint)"/><path d="M4 6.5 Q8 3 12 6.5 L11 8 L9.5 7 L9.5 6 Q8 5.6 6.5 6 L6.5 7 L5 8 Z M5 9 H11 V11.5 H5 Z" fill="#fff"/></svg>
        555-210-4837
      </li>
      <li>
        <svg viewBox="0 0 16 16" aria-label="Mobile"><circle cx="8" cy="8" r="7.5" fill="var(--mint)"/><rect x="5.5" y="3.5" width="5" height="9" rx="1" fill="#fff"/><rect x="6.3" y="4.6" width="3.4" height="5.8" fill="var(--mint)"/></svg>
        555-362-9150
      </li>
      <li>
        <svg viewBox="0 0 16 16" aria-label="Email"><circle cx="8" cy="8" r="7.5" fill="var(--mint)"/><rect x="4" y="5" width="8" height="6" fill="#fff"/><path d="M4 5 L8 8.5 L12 5" stroke="var(--mint)" fill="none"/></svg>
        dmoreau@quennickrx.com
      </li>
    </ul>

    <div class="company">
      <h2 class="company-name">QUENNICK THERAPEUTICS, LLC</h2>
      <p class="company-address">118 Linden Avenue Marlow, GA 30999</p>
    </div>
  </section>
</main>
</body>
</html>
```